Business Name: DM Space Arranging Pty Ltd

Business Type: Professional Home Styling and Minor Renovation Business

Logo: Attached is the logo that has been created.
I always envisaged the logo in the middle of the business card with my full name underneath it.

Marnie Tulloch B.Com LMR HTV
Property Stylist & Project Manager

Include dot points of services
Staging Houses for Sale
Minor Home Renovations
Home Styling & Project Management
Re-Designing Living Spaces to Aid the Disabled

Somewhere on the card I would like to incorporate
"Property Styling and Cosmetic Renovations"

Colour Scheme:
Gloss black business card, with white and then
Gold or Silver as the highlight colours.

Incorporate a small amount of yellow only if possible to make it pop. If this really doesn’t work it doesn’t have to be used. Also l like the colour teal if that needs to be used as a contrast colour.

Feel/Themes
• I love antique chairs, regal expensive looking furniture mixed with modern homes (this is the unique style I want to sell) antique and modern mix that looks high class as well as modern and fresh, targeting an executive market.
• I want to use an orchid as a trademark throughout the course of my work, not sure if this can somehow be incorporated? Also really like crowns to give that regal/antique feel and then something else to give that modern twist (I don’t know what the something else could be)
• Wall Paper Look (on a portion of it not all of it, like a French look)
• Overall feel - A very deluxe and professional feel with a little bit of creative flare.

I hope this helps create a bit of a picture.

Is it ok that I call you tomorrow morning? My mobile number is 0438 926 574 if you have any questions for me in the meantime.

Target Market(s)

High Quality Executive Market - People selling homes

Industry/Entity Type

Business

Contact Information for Business Card

Include dot points of services:
Staging Houses for Sale
Minor Home Renovations

Font styles to use
Serif
Script

Colors
33b8a4
fbed22

Requirements
Must have
• Marnie Tulloch B.Com LMR HTV
• Property Stylist & Project Manager
• LMR and HTV Logos on the card
• "Dramatically increase the value of your property"
Nice to have
• Colour Scheme:
• Gloss black business card, with white and then
• Gold or Silver as the highlight colours.
• Incorporate a small amount of yellow only if possible to make it pop. If this really doesn’t work it doesn’t have to be used. Also l like the colour teal if that needs to be used as a contrast colour.
• Also like teal as a highlight colour.

```html
<!DOCTYPE html>
<html lang="en">
<head>
<meta charset="utf-8">
<title>DM Space Arranging Pty Ltd – Business Card</title>
<link rel="stylesheet" href="https://fonts.googleapis.com/css2?family=Cinzel:wght@400;600&family=Great+Vibes&family=Open+Sans:ital,wght@0,400;1,400&display=swap">
<style>
  :root {
    --backdrop: #b9b9b9;
    --card-black: #0d0d0d;
    --card-black-sheen: #2a2a2a;
    --card-white: #ffffff;
    --ink: #1c1c1c;
    --ink-soft: #3a3a3a;
    --script-grey: #b8b8b8;
    --script-white: #f2f2f2;
    --list-text: #e6e6e6;
    --gold-light: #c9a43a;
    --gold: #a07c16;
    --gold-dark: #5e4608;
    --silver: #8c8c8c;
  }
  * { box-sizing: border-box; margin: 0; padding: 0; }
  html, body {
    width: 1200px;
    height: 871px;
    overflow: hidden;
    background: var(--backdrop);
  }
  .canvas {
    position: relative;
    width: 1200px;
    height: 871px;
  }
  .card {
    position: absolute;
    left: 270px;
    width: 660px;
    height: 366px;
    border-radius: 4px;
    overflow: hidden;
    box-shadow: 0 10px 24px rgba(0, 0, 0, 0.35);
  }

  /* Back of card: services */
  .card--back {
    top: 40px;
    background: linear-gradient(160deg, var(--card-black-sheen) 0%, var(--card-black) 45%, var(--card-black) 100%);
  }
  .tagline {
    position: absolute;
    top: 46px;
    left: 0;
    width: 100%;
    text-align: center;
    font-family: "Great Vibes", cursive;
    line-height: 1.1;
  }
  .tagline__lead {
    display: block;
    font-size: 34px;
    color: var(--script-grey);
  }
  .tagline__main {
    display: block;
    font-size: 50px;
    color: var(--script-white);
  }
  .services {
    position: absolute;
    top: 206px;
    left: 70px;
    right: 40px;
    display: grid;
    grid-template-columns: 230px 1fr;
    row-gap: 16px;
    column-gap: 20px;
    list-style: none;
  }
  .services__item {
    display: flex;
    align-items: center;
    gap: 12px;
    font-family: "Open Sans", sans-serif;
    font-size: 15px;
    color: var(--list-text);
  }
  .services__tick { flex: none; width: 18px; height: 16px; }

  /* Front of card: identity */
  .card--front {
    top: 464px;
    background: var(--card-white);
  }
  .brand {
    position: absolute;
    top: 70px;
    left: 0;
    width: 100%;
    display: flex;
    justify-content: center;
    align-items: center;
    gap: 12px;
  }
  .brand__mark {
    width: 14px;
    height: 14px;
    border-radius: 50%;
    background: var(--silver);
  }
  .brand__name {
    font-family: "Cinzel", serif;
    font-weight: 600;
    font-size: 20px;
    letter-spacing: 2px;
    color: var(--silver);
  }
  .person {
    position: absolute;
    top: 160px;
    left: 0;
    width: 100%;
    text-align: center;
  }
  .person__name {
    font-family: "Cinzel", serif;
    font-weight: 600;
    font-size: 25px;
    letter-spacing: 1px;
    color: var(--ink);
  }
  .person__role {
    margin-top: 6px;
    font-family: "Open Sans", sans-serif;
    font-style: italic;
    font-size: 17px;
    color: var(--ink-soft);
  }
  .gold-band {
    position: absolute;
    left: 0;
    bottom: 0;
    width: 100%;
    height: 48px;
    background: linear-gradient(90deg, var(--gold-dark) 0%, var(--gold-light) 35%, var(--gold) 65%, var(--gold-dark) 100%);
  }
</style>
</head>
<body>
<main class="canvas">

  <section class="card card--back" aria-label="Business card back">
    <h2 class="tagline">
      <span class="tagline__lead">Property Styling</span>
      <span class="tagline__main">and Cosmetic Renovations</span>
    </h2>
    <ul class="services">
      <li class="services__item">
        <svg class="services__tick" viewBox="0 0 18 16" aria-hidden="true"><path d="M1 8 L7 14 L17 1" fill="none" stroke="#c9a43a" stroke-width="3" stroke-linecap="round" stroke-linejoin="round"/></svg>
        Staging Houses for Sale
      </li>
      <li class="services__item">
        <svg class="services__tick" viewBox="0 0 18 16" aria-hidden="true"><path d="M1 8 L7 14 L17 1" fill="none" stroke="#c9a43a" stroke-width="3" stroke-linecap="round" stroke-linejoin="round"/></svg>
        Home Styling &amp; Project Management
      </li>
      <li class="services__item">
        <svg class="services__tick" viewBox="0 0 18 16" aria-hidden="true"><path d="M1 8 L7 14 L17 1" fill="none" stroke="#c9a43a" stroke-width="3" stroke-linecap="round" stroke-linejoin="round"/></svg>
        Minor Home Renovations
      </li>
      <li class="services__item">
        <svg class="services__tick" viewBox="0 0 18 16" aria-hidden="true"><path d="M1 8 L7 14 L17 1" fill="none" stroke="#c9a43a" stroke-width="3" stroke-linecap="round" stroke-linejoin="round"/></svg>
        Re-Designing Living Spaces to Aid the Disabled
      </li>
    </ul>
  </section>

  <section class="card card--front" aria-label="Business card front">
    <div class="brand">
      <span class="brand__mark" aria-hidden="true"></span>
      <span class="brand__name">DM Space Arranging Pty Ltd</span>
    </div>
    <div class="person">
      <h1 class="person__name">Marnie Tulloch B.Com LMR HTV</h1>
      <p class="person__role">Property Stylist &amp; Project Manager</p>
    </div>
    <div class="gold-band" aria-hidden="true"></div>
  </section>

</main>
</body>
</html>
```